Need a brochure design for my business which sells Australian themed Christmas ornaments.

We need a brochure designed for our company called Wattle Lantern Pty Ltd.
Our company sells Australian themed glass Christmas ornaments which have been internally hand painted with designs depicting Australian flora & fauna as well as Indigenous art designs. Our website, www.wattlelantern.com.au will show you the product we sell. We would like a brochure to display our current designs (19 in total). Six of the designs have a front & back image. Each design image will be accompanied with a short description of what the design represents. The ornaments each present with a padded gift box for storage and a descriptive swing tag.
We would like to use the same colours of our website (blue and yellow) and would like to incorporate the company logo. We would like the brochure to communicate that all designs have been reproduced from commissioned art work by Australian Indigenous and non-Indigenous artists. The descriptive words unique, Australian, quality, keepsake, gift and beautiful should all be used.
Our website and contact details are also to be included. (See attached files for reference).
The brochure will be distributed to both wholesale and retail clients..
Updates

Project Deadline Extended
Reason: Additional detail required. Thank you

Target Market(s)

Wholesale and retail gift shop clients

Industry/Entity Type

Retail

Requirements
Must have
• All 19 designs must be depicted. All design descriptions must be included. An image example of the padded gift box and swing tag must be included.
The company Logo must be used, preferably at the top of the page.
Must state that all designs have been reproduced from commissioned artwork by Australian Indigenous and non-Indigenous artists.
The descriptive words: Australian design, unique, internally hand-painted, gift, keepsake and beautiful must be used.
The blue and yellow colours (as depicted on the website) must be used. Ideally the brochure would be a two page document (front and back) of one sheet but I will leave the size up to you depending on the design.
Website and contact details.

```html
<!DOCTYPE html>
<html lang="en">
<head>
<meta charset="utf-8">
<title>Wattle Lantern – Brochure Pages</title>
<link rel="stylesheet" href="https://fonts.googleapis.com/css2?family=Open+Sans:wght@400;600&family=Dancing+Script:wght@500&display=swap">
<style>
  :root {
    --backdrop: #2f3234;
    --paper: #f1e7a6;
    --paper-top: #f4ecb8;
    --brand-blue: #1c4a9a;
    --brand-orange: #dc8e2e;
    --copy-orange: #e0782c;
    --ink: #1d1d1d;
    --white: #ffffff;
    --photo-sand: #bba58e;
  }
  * { box-sizing: border-box; margin: 0; padding: 0; }
  html, body { width: 1200px; height: 900px; overflow: hidden; }
  body {
    background: var(--backdrop);
    font-family: "Open Sans", Arial, sans-serif;
    position: relative;
  }
  .page { position: absolute; background: var(--paper); overflow: hidden; }
  .page--intro { left: 79px; top: 55px; width: 467px; height: 661px; }
  .page--design { left: 609px; top: 188px; width: 468px; height: 664px; }

  .page__top { position: absolute; left: 0; top: 0; width: 100%; background: var(--paper-top); }
  .rule { position: absolute; left: 0; width: 100%; height: 7px; background: var(--brand-orange); }

  .masthead { position: absolute; left: 0; background: var(--brand-blue); color: var(--white); }
  .brand { position: absolute; display: flex; align-items: center; gap: 9px; }
  .brand__mark { width: 56px; height: 56px; background: var(--white); flex: none; }
  .brand__name { font-size: 16px; font-weight: 600; color: var(--white); white-space: nowrap; }

  .intro-copy { position: absolute; left: 21px; top: 106px; width: 205px; font-size: 9px; line-height: 1.45; }
  .range { list-style: none; position: absolute; left: 19px; top: 175px; font-size: 9px; }
  .range li { display: flex; align-items: center; gap: 9px; height: 25px; }
  .range__dot { width: 5px; height: 5px; border-radius: 50%; background: var(--brand-orange); flex: none; }

  .photo { position: absolute; }
  .photo--pendant {
    left: 234px; top: 47px; width: 233px; height: 280px;
    background: radial-gradient(ellipse at 55% 60%, #5a8fb0 0 18%, transparent 19%),
                linear-gradient(160deg, #d8c0aa, #c4a892 60%, #efece8 100%);
  }
  .photo-frame {
    position: absolute; left: 72px; top: 168px; width: 321px; height: 241px;
    background: var(--white); padding: 5px;
  }
  .photo--ornament {
    position: static; width: 100%; height: 100%;
    background: radial-gradient(circle at 50% 52%, #c2332a 0 16%, #eadbcf 17% 38%, var(--photo-sand) 39%);
  }

  .body-copy { position: absolute; color: var(--copy-orange); font-size: 9.6px; line-height: 1.35; width: 420px; }
  .body-copy p + p { margin-top: 12px; }

  .design-panel {
    position: absolute; left: 234px; top: 43px; width: 234px; height: 102px;
    background: var(--brand-orange); color: var(--white); padding: 16px 20px;
  }
  .design-panel__title { font-family: "Dancing Script", cursive; font-weight: 500; font-size: 23px; line-height: 1; margin-bottom: 12px; }
  .design-panel__story { font-size: 9.5px; line-height: 1.4; }

  .contact {
    position: absolute; left: 22px; display: flex; align-items: center;
    font-size: 8.2px; color: var(--ink); white-space: nowrap;
  }
  .contact__item { display: flex; align-items: center; gap: 3px; margin-right: 10px; }
  .contact__item:last-child { margin-right: 0; }
  .contact__item--name { font-weight: 600; margin-right: 4px; }
  .contact__dot { width: 5px; height: 5px; border-radius: 50%; background: var(--brand-blue); flex: none; }
</style>
</head>
<body>

<section class="page page--intro">
  <div class="page__top" style="height:40px"></div>
  <div class="rule" style="top:40px"></div>
  <header class="masthead" style="top:47px;width:234px;height:280px">
    <div class="brand" style="left:22px;top:30px">
      <span class="brand__mark"></span>
      <span class="brand__name">Wattle Lantern</span>
    </div>
    <p class="intro-copy">Wattle Lantern Pty Ltd is proud to produce a unique range of HAND-PAINTED glass ornaments. The designs are reproduced exclusively for Wattle Lantern Pty Ltd. Our current range includes:</p>
    <ul class="range">
      <li><span class="range__dot"></span>AUSTRALIAN INDIGENOUS: aboriginal design</li>
      <li><span class="range__dot"></span>TRADITIONAL AUSTRALIAN: non-Indigenous</li>
      <li><span class="range__dot"></span>CORPORATE: Company logo or design</li>
    </ul>
  </header>
  <div class="photo photo--pendant" role="img" aria-label="Photo of a hand-painted glass pendant with a wildflower landscape, worn on a silver chain"></div>
  <div class="body-copy" style="left:26px;top:346px">
    <p>Our ornaments beautifully represent all things which are uniquely Australian.<br>They are an ideal gift for loved ones or just perfect for decorating a favourite place at home, office or family Christmas tree. Similarly, collectors will find the allure of these hand-crafted items irresistible.</p>
    <p>These internal-painted glass ornaments are a keepsake to be treasured from generation to generation. Each ornament is presented in its own padded gift box. This presentation gift box is covered in a beautiful Australian Aboriginal design fabric.</p>
  </div>
  <div class="rule" style="top:619px"></div>
  <footer class="contact" style="top:638px">
    <span class="contact__item contact__item--name">WATTLE LANTERN</span>
    <span class="contact__item"><span class="contact__dot"></span>PO BOX 4817. BRISBANE. QLD. 4000</span>
    <span class="contact__item"><span class="contact__dot"></span>PH: +61-7-35550142</span>
    <span class="contact__item"><span class="contact__dot"></span>FAX: +61-7-35550187</span>
  </footer>
</section>

<section class="page page--design">
  <div class="page__top" style="height:43px"></div>
  <div class="rule" style="top:43px"></div>
  <header class="masthead" style="top:49px;width:234px;height:96px">
    <div class="brand" style="left:23px;top:21px">
      <span class="brand__mark"></span>
      <span class="brand__name">Wattle Lantern</span>
    </div>
  </header>
  <div class="design-panel">
    <h2 class="design-panel__title">Wandering Creek</h2>
    <p class="design-panel__story">Carved the creeks across the dry plain.<br>Now he rests beneath the red gums.</p>
  </div>
  <div class="photo-frame">
    <div class="photo photo--ornament" role="img" aria-label="Photo of a glass bauble painted with a red coiled serpent on a dotted Aboriginal-style background"></div>
  </div>
  <div class="body-copy" style="left:29px;top:434px">
    <p>Our ornaments beautifully represent all things which are uniquely Australian.<br>They are an ideal gift for loved ones or just perfect for decorating a favourite place at home, office or family Christmas tree. Similarly, collectors will find the allure of these hand-crafted items irresistible.</p>
    <p>These internal-painted glass ornaments are a keepsake to be treasured from generation to generation. Each ornament is presented in its own padded gift box. This presentation gift box is covered in a beautiful Australian Aboriginal design fabric.</p>
  </div>
  <div class="rule" style="top:620px"></div>
  <footer class="contact" style="top:639px">
    <span class="contact__item contact__item--name">WATTLE LANTERN</span>
    <span class="contact__item"><span class="contact__dot"></span>PO BOX 4817. BRISBANE. QLD. 4000</span>
    <span class="contact__item"><span class="contact__dot"></span>PH: +61-7-35550142</span>
    <span class="contact__item"><span class="contact__dot"></span>FAX: +61-7-35550187</span>
  </footer>
</section>

</body>
</html>
```